Gin bottle label

We need a complete gin bottle complete label design - with front and back or wrap-around labels. Please see attached presentation for details.

```html
<!DOCTYPE html>
<html lang="en">
<head>
<meta charset="utf-8">
<title>Dynamo Town Gin – Label</title>
<link href="https://fonts.googleapis.com/css2?family=Oswald:wght@700&family=Playfair+Display:wght@600&family=Libre+Baskerville&family=Montserrat:wght@600&display=swap" rel="stylesheet">
<style>
  :root{
    --bg:#f4f4f2;
    --ink:#1f1f1f;
    --cream:#ece2c6;
    --cream-deep:#d9cba6;
    --sepia:#8a7558;
    --sepia-dark:#3d3128;
    --line:#9a8a6c;
  }
  *{margin:0;padding:0;box-sizing:border-box}
  html,body{width:1200px;height:900px;overflow:hidden;background:var(--bg)}
  .canvas{position:relative;width:1200px;height:900px}

  .front-label{position:absolute;left:330px;top:150px;width:420px;height:600px}
  .front-label svg.frame{position:absolute;inset:0}
  .badge{position:absolute;left:50%;top:0;transform:translate(-50%,-12px)}

  .schematic-area{position:absolute;left:40px;top:300px;width:340px;height:250px;
    border-radius:50% 50% 8px 8px;
    background:radial-gradient(ellipse at 50% 45%, rgba(154,138,108,.28), rgba(154,138,108,.08) 60%, transparent 75%)}
  .portrait-area{position:absolute;left:120px;top:345px;width:180px;height:215px;
    border-radius:90px 90px 0 0;
    background:linear-gradient(180deg,var(--sepia) 0%,#5e4d3e 55%,var(--sepia-dark) 100%)}

  .maker{position:absolute;left:0;right:0;top:80px;text-align:center;
    font-family:"Playfair Display",serif;font-weight:600;color:var(--ink);
    font-size:22px;letter-spacing:1px;line-height:1}
  .maker-sub{display:block;margin:6px auto 0;width:110px;border-top:1px solid var(--ink);
    padding-top:3px;font-family:"Montserrat",sans-serif;font-size:6px;letter-spacing:1.5px}

  .product-name{position:absolute;left:0;right:0;top:128px;text-align:center;
    font-family:"Oswald",sans-serif;font-weight:700;color:var(--ink);
    font-size:88px;line-height:.92;letter-spacing:1px;transform:scaleX(.85)}

  .volume,.strength{position:absolute;top:530px;font-family:"Libre Baskerville",serif;
    font-size:15px;color:var(--ink)}
  .volume{left:34px}
  .strength{right:34px}

  .neck-label{position:absolute;left:880px;top:190px;width:78px;height:470px}
  .neck-label .strip{position:absolute;inset:0;background:var(--cream);
    border-left:10px solid var(--ink);border-right:10px solid var(--ink)}
  .neck-text{position:absolute;left:50%;top:50%;transform:translate(-50%,-50%) rotate(-90deg);
    white-space:nowrap;text-align:center;font-family:"Playfair Display",serif;font-weight:600;
    font-size:20px;color:var(--ink);line-height:1}
  .neck-text small{display:block;font-family:"Montserrat",sans-serif;font-size:6px;letter-spacing:1.5px;margin-top:5px}
</style>
</head>
<body>
<main class="canvas">

  <section class="front-label">
    <svg class="frame" width="420" height="600" viewBox="0 0 420 600">
      <path d="M0 110 C0 55 110 18 210 16 C310 18 420 55 420 110 V600 H0 Z" fill="var(--ink)"/>
      <path d="M8 114 C8 64 112 28 210 26 C308 28 412 64 412 114 V592 H8 Z" fill="var(--cream)"/>
      <path d="M24 122 C24 78 118 46 210 44 C302 46 396 78 396 122 V572 H24 Z" fill="none" stroke="var(--line)" stroke-width="1.5"/>
    </svg>

    <div class="schematic-area" role="img" aria-label="Faint sepia technical drawing of an electric motor with coils"></div>
    <div class="portrait-area" role="img" aria-label="Vintage sepia portrait photograph of an inventor in a dark suit"></div>

    <svg class="badge" width="56" height="56" viewBox="0 0 56 56">
      <circle cx="28" cy="28" r="26" fill="var(--ink)"/>
      <circle cx="28" cy="28" r="20" fill="none" stroke="var(--cream-deep)" stroke-width="2"/>
    </svg>

    <div class="maker">Harrowgate Distillery
      <span class="maker-sub">COMPANY LIMITED</span>
    </div>

    <h1 class="product-name">DYNAMO<br>TOWN GIN</h1>

    <span class="volume">750mL</span>
    <span class="strength">46% ABV</span>
  </section>

  <aside class="neck-label">
    <div class="strip"></div>
    <div class="neck-text">Harrowgate Distillery<small>COMPANY LIMITED</small></div>
  </aside>

</main>
</body>
</html>
```